Valmora Company needs a Business Card Design

We just opened our business recently and we need a business card design. Our basic product are clothes and accessories. We would like to see designs that use bright colors like pink, light blue and purple. In addition to that kindly include also our address in the business card which our main office is located in Los Angeles, California.
The final design should communicate that we have affordable price yet high quality brand.

Target Market(s)

young and middle age women

Industry/Entity Type

Business

Contact Information for Business Card

Valmora Apparel and Accessories 4873 North Bellcrest St. Port Calloway Westmark
Tel: 555-318-6492

Logo Text

Valmora's Apparel and Accessories

Font styles to use
Serif

Requirements
Must have
• there should be a graphic of a sexy lady wearing an elegant dress at the upper left corner of the business card.

```html
<!DOCTYPE html>
<html lang="en">
<head>
<meta charset="utf-8">
<title>Valmora Apparel and Accessories – Business Card</title>
<link rel="stylesheet" href="https://fonts.googleapis.com/css2?family=Alegreya:ital,wght@0,400;0,700;1,400&display=swap">
<style>
  :root {
    --page-bg: #ece8ea;
    --magenta-deep: #b43aa5;
    --magenta: #cc4cbd;
    --magenta-light: #dc6bcf;
    --paper: #ffffff;
    --ink-light: #ffffff;
    --figure-dark: #2a2a2a;
    --figure-mid: #6a6a6a;
  }
  html, body {
    margin: 0;
    padding: 0;
    width: 1200px;
    height: 818px;
    overflow: hidden;
    background: var(--page-bg);
  }
  .canvas {
    position: relative;
    width: 1200px;
    height: 818px;
    display: flex;
    align-items: center;
    justify-content: center;
  }
  .business-card {
    position: relative;
    width: 1000px;
    height: 572px;
    background: linear-gradient(135deg, var(--magenta-deep) 0%, var(--magenta-light) 45%, var(--magenta) 100%);
    box-shadow: 0 14px 40px rgba(60, 20, 55, 0.25);
    overflow: hidden;
    font-family: "Alegreya", Georgia, serif;
    color: var(--ink-light);
  }
  .photo-panel {
    position: absolute;
    left: 70px;
    top: 0;
    width: 360px;
    height: 100%;
    background: var(--paper);
  }
  .lady-illustration {
    position: absolute;
    left: 90px;
    top: 40px;
    width: 170px;
    height: 500px;
    border-radius: 70px 70px 20px 20px;
    background: linear-gradient(180deg, var(--figure-dark) 0%, var(--figure-mid) 100%);
  }
  .brand {
    position: absolute;
    left: 490px;
    top: 70px;
  }
  .brand-name {
    margin: 0;
    font-size: 44px;
    font-weight: 400;
    letter-spacing: 0.62em;
    line-height: 1;
  }
  .brand-tagline {
    margin: 18px 0 0;
    font-size: 34px;
    line-height: 1;
    font-weight: 400;
  }
  .brand-tagline strong {
    font-weight: 700;
  }
  .contact {
    position: absolute;
    left: 560px;
    top: 330px;
    margin: 0;
    padding: 0;
    list-style: none;
    font-size: 24px;
    line-height: 1.35;
  }
  .contact-item {
    display: flex;
    align-items: flex-start;
    gap: 18px;
    margin-bottom: 14px;
  }
  .contact-icon {
    flex: none;
    width: 34px;
    height: 34px;
    background: var(--paper);
    display: flex;
    align-items: center;
    justify-content: center;
  }
  .contact-icon svg {
    width: 22px;
    height: 22px;
    fill: var(--magenta);
  }
</style>
</head>
<body>
<main class="canvas">
  <section class="business-card" aria-label="Valmora Apparel and Accessories business card">
    <div class="photo-panel">
      <div class="lady-illustration" role="img" aria-label="Silhouette illustration of an elegant lady in a fitted dress holding a pink handbag"></div>
    </div>

    <header class="brand">
      <h1 class="brand-name">Valmora</h1>
      <p class="brand-tagline"><strong>Apparel</strong> and <strong>Accessories</strong></p>
    </header>

    <ul class="contact">
      <li class="contact-item">
        <span class="contact-icon">
          <svg viewBox="0 0 24 24" aria-hidden="true"><path d="M6.6 10.8a15.1 15.1 0 0 0 6.6 6.6l2.2-2.2a1 1 0 0 1 1-.25 11.4 11.4 0 0 0 3.6.57 1 1 0 0 1 1 1V20a1 1 0 0 1-1 1A17 17 0 0 1 3 4a1 1 0 0 1 1-1h3.5a1 1 0 0 1 1 1c0 1.25.2 2.45.57 3.6a1 1 0 0 1-.25 1z"/></svg>
        </span>
        <span class="contact-text">555-318-6492</span>
      </li>
      <li class="contact-item">
        <span class="contact-icon">
          <svg viewBox="0 0 24 24" aria-hidden="true"><path d="M12 2a7 7 0 0 0-7 7c0 5.2 7 13 7 13s7-7.8 7-13a7 7 0 0 0-7-7zm0 9.5A2.5 2.5 0 1 1 12 6.5a2.5 2.5 0 0 1 0 5z"/></svg>
        </span>
        <span class="contact-text">4873 North Bellcrest St.<br><em>Port Calloway Westmark</em></span>
      </li>
    </ul>
  </section>
</main>
</body>
</html>
```